New Innovative Counselling and psychotherapy Service needs Business Card design

Keep it simple and professional. On one side, just company name and logo (perhaps in all blue) and maybe a tag line.

On other side (all white) my name and Qualifications in centre

Industry/Entity Type

Health And Wellness

Contact Information for Business Card

Dara Whelby
Counsellor & Psychotherapist
BSc (Psychol.), BA, Dip. (Couns. & Psych.), PG.Cert (CBT), FGTrK, ONRE

I will also require Mobile no, Email and web site address of which I'll pass on to final designer.

Font styles to use
Sans Serif

Requirements
Must have
• My Logo Only and please use the colours in logo that is in it.
Should not have
• Any other images

```html
<!DOCTYPE html>
<html lang="en">
<head>
<meta charset="utf-8">
<title>Brightwell Lane – Business Card</title>
<link rel="stylesheet" href="https://fonts.googleapis.com/css2?family=Open+Sans:wght@300;400;600&display=swap">
<style>
  :root {
    --canvas: #2a2a2b;
    --card-dark: #303133;
    --card-dark-hi: #3d3e41;
    --white: #ffffff;
    --sky: #5ab3e6;
    --sky-light: #7ec6ee;
    --text-light: #e9e9ea;
  }
  * { margin: 0; padding: 0; box-sizing: border-box; }
  html, body { width: 1200px; height: 896px; overflow: hidden; }
  body {
    background: var(--canvas);
    font-family: "Open Sans", Arial, sans-serif;
    position: relative;
  }
  .card {
    position: absolute;
    top: 293px;
    width: 520px;
    height: 310px;
    border-radius: 18px;
    overflow: hidden;
    background: linear-gradient(135deg, var(--card-dark-hi) 0%, var(--card-dark) 60%, #2b2c2e 100%);
    box-shadow: 0 10px 28px rgba(0,0,0,.45);
  }
  .card--front { left: 50px; }
  .card--back { left: 630px; }

  /* front */
  .brand {
    position: absolute;
    left: 0; right: 0; top: 50%;
    transform: translateY(-50%);
    display: flex;
    align-items: center;
    justify-content: center;
    gap: 16px;
  }
  .brand__dot {
    width: 46px; height: 46px;
    border-radius: 50%;
    background: var(--sky);
  }
  .brand__name {
    font-weight: 300;
    font-size: 38px;
    letter-spacing: .2px;
    color: var(--white);
  }

  /* back */
  .back__shape { position: absolute; left: 0; top: 0; }
  .back__mark {
    position: absolute;
    left: 40px; top: 205px;
    display: flex; align-items: center; gap: 10px;
  }
  .back__mark .brand__dot { width: 26px; height: 26px; }
  .back__mark .brand__name { font-size: 24px; color: var(--sky); font-weight: 400; }

  .details {
    position: absolute;
    left: 262px; top: 34px;
    color: var(--text-light);
  }
  .details__company { font-weight: 300; font-size: 22px; color: var(--white); line-height: 1.1; }
  .details__person {
    font-weight: 400; font-size: 22px; color: var(--sky);
    text-transform: uppercase; margin-top: 10px; line-height: 1.05;
  }
  .details__role, .details__quals { font-size: 10.5px; line-height: 1.4; }
  .details__role { margin-top: 2px; }

  .contact {
    position: absolute;
    left: 360px; top: 208px;
    list-style: none;
    color: var(--text-light);
    font-size: 10.5px;
    line-height: 1.75;
  }
  .contact li { display: flex; align-items: center; gap: 6px; }
  .contact svg { width: 9px; height: 9px; fill: none; stroke: var(--text-light); stroke-width: 1.4; }
</style>
</head>
<body>

<section class="card card--front" aria-label="Card front">
  <div class="brand">
    <span class="brand__dot"></span>
    <span class="brand__name">Brightwell Lane</span>
  </div>
</section>

<section class="card card--back" aria-label="Card back">
  <svg class="back__shape" width="520" height="310" viewBox="0 0 520 310">
    <path d="M 96 122 A 226 226 0 0 1 348 300" fill="none" stroke="var(--sky)" stroke-width="5"/>
    <circle cx="120" cy="345" r="222" fill="var(--white)"/>
  </svg>
  <div class="back__mark">
    <span class="brand__dot"></span>
    <span class="brand__name">Brightwell Lane</span>
  </div>

  <div class="details">
    <p class="details__company">Brightwell Lane</p>
    <p class="details__person">Dara Whelby</p>
    <p class="details__role">Counsellor &amp; Psychotherapist</p>
    <p class="details__quals">BSc (Psychol.), BA, Dip.<br>(Couns. &amp; Psych.), PG.Cert<br>(CBT), FGTrK, ONRE</p>
  </div>

  <ul class="contact">
    <li><svg viewBox="0 0 10 10"><path d="M2 1 L4 1 L4.6 3 L3.4 3.8 Q4.6 6 6.2 6.6 L7 5.4 L9 6 L9 8 Q5 9 2 5 Q1 3 2 1 Z"/></svg>555-014-2786</li>
    <li><svg viewBox="0 0 10 10"><rect x="1" y="2" width="8" height="6"/><path d="M1 2 L5 5.5 L9 2"/></svg>info@brightwelllane.com</li>
    <li><svg viewBox="0 0 10 10"><circle cx="5" cy="5" r="4"/><path d="M1 5 H9 M5 1 Q2.5 5 5 9 M5 1 Q7.5 5 5 9"/></svg>www.brightwelllane.com</li>
  </ul>
</section>

</body>
</html>
```